Velvet Lantern rebranding my business with a new business card

I have my new logo and now I need a refresher on my business cards. I really want something fun and fresh. I like black background or anything to make the color pop.
Logo
Name: Velvet Lantern
Contact Info as stated below:
Mira Pellow
555-013-4762
Logo
Name: Velvet Lantern
Mira Pellow
555-013-4762
fb.me/VelvetLanternbyMira
Instagram: @VelvetLanternbyMira

Industry/Entity Type

Business

Contact Information for Business Card

double-sided. Logo on one side. Contact info on the other.

Requirements
Must have
• Logo
• Name: Velvet Lantern
• Contact Info as stated below:
• Mira Pellow
• 555-013-4762
• fb.me/VelvetLanternbyMira
• fb.me/VelvetLanternbyMira

```html
<!DOCTYPE html>
<html lang="en">
<head>
<meta charset="utf-8">
<title>Velvet Lantern – Business Card</title>
<link href="https://fonts.googleapis.com/css2?family=Work+Sans:wght@400;500;600&display=swap" rel="stylesheet">
<style>
  :root {
    --backdrop: #e6e6e6;
    --card-white: #ffffff;
    --teal: #35b9a2;
    --teal-back: #3fc0aa;
    --pink: #c672b0;
    --ink: #2e2e2e;
    --ink-soft: #555555;
  }
  * { margin: 0; padding: 0; box-sizing: border-box; }
  html, body {
    width: 1200px; height: 1000px; overflow: hidden;
    background: var(--backdrop);
    font-family: "Work Sans", Arial, sans-serif;
  }
  .card {
    position: absolute; left: 240px; width: 696px; height: 398px;
    border-radius: 14px; overflow: hidden;
  }
  .card--front { top: 82px; background: var(--card-white); }
  .card--back { top: 520px; background: var(--teal-back); }

  .contact { position: absolute; left: 82px; top: 98px; }
  .contact__name {
    color: var(--teal); font-size: 21px; font-weight: 500; letter-spacing: 1.6px;
    line-height: 26px;
  }
  .contact__role { color: var(--ink); font-size: 16px; line-height: 20px; }
  .contact__list { list-style: none; position: absolute; top: 88px; left: 0; }
  .contact__item {
    display: flex; align-items: center; height: 22px;
    color: var(--ink-soft); font-size: 16px; white-space: nowrap;
  }
  .contact__item--social { margin-top: 48px; }
  .contact__icon { width: 12px; height: 14px; margin-right: 12px; flex: none; }
  .contact__dot {
    width: 11px; height: 11px; margin-right: 7px; flex: none;
    background: var(--teal); border-radius: 2px;
  }

  .wordmark {
    position: absolute; display: flex; flex-direction: column;
    align-items: center; justify-content: center; text-align: center;
    font-weight: 600; font-size: 34px; line-height: 40px; letter-spacing: 1px;
  }
  .wordmark--front { left: 385px; top: 70px; width: 250px; height: 240px; color: var(--pink); }
  .wordmark--back { left: 223px; top: 78px; width: 250px; height: 240px; color: #ffffff; }

  .card__band { position: absolute; left: 0; bottom: 0; width: 696px; height: 40px; }
</style>
</head>
<body>
  <section class="card card--front" aria-label="Business card front">
    <div class="contact">
      <p class="contact__name">MIRA PELLOW</p>
      <p class="contact__role">Owner</p>
      <ul class="contact__list">
        <li class="contact__item">
          <svg class="contact__icon" viewBox="0 0 12 14" aria-hidden="true">
            <rect x="2.5" y="0.8" width="7" height="12.4" rx="1.4" fill="none" stroke="#35b9a2" stroke-width="1.5"/>
            <line x1="5" y1="11" x2="7" y2="11" stroke="#35b9a2" stroke-width="1.2"/>
          </svg>555-013-4762
        </li>
        <li class="contact__item">
          <svg class="contact__icon" viewBox="0 0 12 14" aria-hidden="true">
            <rect x="0.5" y="3" width="11" height="8" rx="1" fill="#35b9a2"/>
            <path d="M0.8 3.5 L6 7.5 L11.2 3.5" fill="none" stroke="#ffffff" stroke-width="1"/>
          </svg>info@mirapellow.com
        </li>
        <li class="contact__item contact__item--social">
          <span class="contact__dot" aria-hidden="true"></span>me/VelvetLanternbyMira
        </li>
      </ul>
    </div>

    <div class="wordmark wordmark--front" role="img" aria-label="Velvet Lantern logo">
      <span>Velvet</span><span>Lantern</span>
    </div>

    <svg class="card__band" viewBox="0 0 696 40" aria-hidden="true">
      <rect x="0" y="18" width="408" height="5" fill="#c672b0"/>
      <path d="M0 28 L400 28 C425 28 430 10 460 10 L696 10 L696 40 L0 40 Z" fill="#35b9a2"/>
    </svg>
  </section>

  <section class="card card--back" aria-label="Business card back">
    <div class="wordmark wordmark--back" role="img" aria-label="Velvet Lantern logo">
      <span>Velvet</span><span>Lantern</span>
    </div>
  </section>
</body>
</html>
```